Business Card Design

Carl Brenton Insurance Agency, an Independent Insurance Agency which was stated on Pine Street in Laplace, Louisiana on 1958 and has grown the six locations throughout South Louisiana. We sell personal (auto Homeowners flood, liability) and commercial insurance (commercial property, general liability, workers compensation, commercial auto). I am looking for a double sided card with list the five remaining locations on the back or maybe even a folded four sided card. Our home office is a two story building with a green roof. I have had a logo designed which I have attached. Open for revisions but would like to stay with in the same green roof over an M. I have attached the logo but can not tell if I was uploaded.

Target Market(s)

Individual and commercial insurance buyers. Upper income and business owners

Industry/Entity Type

Insurance

Requirements
Must have
• Must have similar logo as uploaded. Green roof over M or something similar. List all location address and phone numbers.

Employee name, office phone number; direct phone line; email address and website list all locations on card. Very Similar colors to current logo.
Nice to have
• Possible folded card with double sided print

```html
<!DOCTYPE html>
<html lang="en">
<head>
<meta charset="utf-8">
<title>Carl Brenton Insurance Agency – Business Card</title>
<link rel="stylesheet" href="https://fonts.googleapis.com/css2?family=Roboto+Condensed:wght@400;700&family=Roboto:wght@400;500&display=swap">
<style>
  :root {
    --page-bg: #e9e7e2;
    --card-bg: #ffffff;
    --brand-green: #1f6b47;
    --brand-blue: #1f7fc4;
    --tagline-grey: #5f6f66;
    --text-dark: #3a4a44;
    --rule-blue: #4b97d1;
  }
  * { box-sizing: border-box; margin: 0; padding: 0; }
  html, body {
    width: 1200px; height: 885px; overflow: hidden;
    background: var(--page-bg);
    font-family: "Roboto", Arial, sans-serif;
  }
  .sheet {
    width: 1200px; height: 885px;
    display: flex; flex-direction: column; align-items: center; justify-content: center;
    gap: 40px;
  }
  .card {
    position: relative;
    width: 660px; height: 378px;
    background: var(--card-bg);
    border-radius: 18px;
    box-shadow: 0 6px 18px rgba(0,0,0,0.14);
    overflow: hidden;
  }

  /* Front (contact side) */
  .brand {
    position: absolute; left: 36px; top: 116px;
    display: flex; align-items: flex-start; gap: 10px;
  }
  .brand-square {
    width: 24px; height: 24px; background: var(--brand-green); margin-top: 4px;
  }
  .brand-name {
    font-family: "Roboto Condensed", Arial, sans-serif;
    font-weight: 700; color: var(--brand-green);
    font-size: 25px; line-height: 1.0; text-transform: uppercase;
  }
  .brand-tagline {
    font-family: "Roboto Condensed", Arial, sans-serif;
    font-weight: 700; color: var(--tagline-grey);
    font-size: 14px; margin-top: 5px;
  }
  .brand-towns {
    font-size: 7.5px; color: var(--text-dark); margin-top: 4px; letter-spacing: 0.5px;
  }
  .employee-name {
    position: absolute; right: 44px; top: 150px;
    font-family: "Roboto Condensed", Arial, sans-serif;
    font-size: 21px; color: var(--brand-green); letter-spacing: 0.5px;
  }
  .divider {
    position: absolute; left: 300px; right: 40px; top: 184px;
    height: 1px; background: var(--rule-blue);
  }
  .contacts {
    position: absolute; left: 300px; top: 232px;
    list-style: none; display: flex; flex-direction: column; gap: 6px;
  }
  .contact {
    display: flex; align-items: center; gap: 9px;
    font-family: "Roboto Condensed", Arial, sans-serif;
    color: var(--brand-blue); font-size: 16px;
  }
  .contact-email { font-size: 20px; }
  .contact svg { width: 14px; height: 14px; flex: none; }
  .website {
    position: absolute; right: 44px; top: 250px;
    display: flex; align-items: center; gap: 9px;
    font-family: "Roboto Condensed", Arial, sans-serif;
    color: var(--brand-blue); font-size: 18px;
  }
  .website svg { width: 14px; height: 14px; }

  /* Back (brand side) */
  .card-back {
    background: linear-gradient(135deg, #ffffff 0%, #efefef 100%);
    display: flex; align-items: center; justify-content: center;
  }
  .back-brand { display: flex; align-items: flex-start; gap: 18px; }
  .back-brand .brand-square { width: 42px; height: 42px; margin-top: 8px; }
  .back-brand .brand-name { font-size: 46px; }
  .back-brand .brand-tagline { font-size: 24px; margin-top: 10px; }
</style>
</head>
<body>
<main class="sheet">

  <section class="card card-front" aria-label="Card front">
    <div class="brand">
      <div class="brand-square"></div>
      <div>
        <div class="brand-name">Carl Brenton<br>Insurance Agency</div>
        <div class="brand-tagline">Serving Pine Street Since 1962</div>
        <div class="brand-towns">Ashford • Belmont • Cedar Bay • Dunmore • Elkton • Fairview</div>
      </div>
    </div>

    <div class="employee-name">EMPLOYEE NAME</div>
    <div class="divider"></div>

    <ul class="contacts">
      <li class="contact">
        <svg viewBox="0 0 16 16" aria-hidden="true"><path fill="#1f6b47" d="M3 2h3l1 3-2 1a8 8 0 0 0 5 5l1-2 3 1v3a1 1 0 0 1-1 1A12 12 0 0 1 2 3a1 1 0 0 1 1-1z"/></svg>
        xxx xxxx xxxx
      </li>
      <li class="contact">
        <svg viewBox="0 0 16 16" aria-hidden="true"><rect x="2" y="2" width="12" height="12" fill="none" stroke="#1f6b47" stroke-width="1.6"/></svg>
        xxx xxxx xxxx
      </li>
      <li class="contact contact-email">
        <svg viewBox="0 0 16 16" aria-hidden="true"><rect x="1" y="3" width="14" height="10" fill="#1f6b47"/><path d="M1 3l7 6 7-6" fill="none" stroke="#fff" stroke-width="1.4"/></svg>
        info@youremail.com
      </li>
    </ul>

    <div class="website">
      <svg viewBox="0 0 16 16" aria-hidden="true"><circle cx="8" cy="8" r="7" fill="#1f6b47"/><path d="M1 8h14M8 1c3 3 3 11 0 14M8 1c-3 3-3 11 0 14" fill="none" stroke="#fff" stroke-width="1"/></svg>
      www.yourwebsite.com
    </div>
  </section>

  <section class="card card-back" aria-label="Card back">
    <div class="back-brand">
      <div class="brand-square"></div>
      <div>
        <div class="brand-name">Carl Brenton<br>Insurance Agency</div>
        <div class="brand-tagline">Serving Pine Street Since 1962</div>
      </div>
    </div>
  </section>

</main>
</body>
</html>
```